Corporate Business Card

Very professional, Modern, Not to busy, include phone address email, website
(253) 617-4930, 18761 52nd Avenue S, Kent, WA 98047, martin@plumlinegroup.com, varkoworks.com

Target Market(s)

Manufacturing

Industry/Entity Type

Aero, machining, manufacturing, Off road racing

Contact Information for Business Card

Phone, address email, website

```html
<!DOCTYPE html>
<html lang="en">
<head>
<meta charset="utf-8">
<title>Varko Works – Business Card</title>
<link rel="stylesheet" href="https://fonts.googleapis.com/css2?family=Arimo:wght@400;700&display=swap">
<style>
  :root {
    --bg: #e6e6e6;
    --card: #353535;
    --card-deep: #2b2b2b;
    --white: #ffffff;
    --red: #d21f26;
    --rule: #cfcfcf;
  }
  * { margin: 0; padding: 0; box-sizing: border-box; }
  html, body { width: 1200px; height: 801px; overflow: hidden; }
  body {
    background: var(--bg);
    font-family: "Arimo", Arial, sans-serif;
    display: flex;
    align-items: center;
    justify-content: center;
    gap: 44px;
  }
  .card {
    position: relative;
    width: 520px;
    height: 297px;
    background: var(--card);
    color: var(--white);
    box-shadow: 0 6px 18px rgba(0,0,0,0.18);
    overflow: hidden;
  }

  /* front */
  .brand {
    position: absolute;
    top: 34px;
    left: 170px;
    display: flex;
    align-items: center;
    gap: 10px;
    white-space: nowrap;
  }
  .brand-mark { width: 12px; height: 12px; background: var(--red); flex: none; }
  .brand-name {
    font-size: 32px;
    font-weight: 700;
    letter-spacing: 1px;
    color: var(--white);
    text-transform: uppercase;
    white-space: nowrap;
    line-height: 1;
  }
  .rule { position: absolute; height: 1px; background: var(--rule); }
  .rule-brand { top: 84px; left: 150px; width: 190px; }
  .rule-main { top: 162px; left: 44px; width: 440px; }

  .person { position: absolute; left: 44px; top: 108px; }
  .person-name {
    color: var(--red);
    font-size: 21px;
    font-weight: 400;
    text-transform: uppercase;
    letter-spacing: 0.5px;
    line-height: 1.1;
  }
  .person-title { font-size: 15px; margin-top: 3px; }

  .contacts { position: absolute; left: 44px; top: 176px; list-style: none; }
  .contacts li {
    display: flex;
    align-items: center;
    gap: 10px;
    font-size: 15px;
    line-height: 24px;
    white-space: nowrap;
  }
  .contacts svg { width: 13px; height: 13px; fill: var(--red); flex: none; }

  .address {
    position: absolute;
    right: 36px;
    top: 178px;
    text-align: right;
    font-size: 15px;
    line-height: 22px;
    font-style: normal;
    white-space: nowrap;
  }

  /* back */
  .card-back { background: var(--card-deep); }
  .pattern-field {
    position: absolute;
    inset: 0;
    background: linear-gradient(135deg, #2a2a2a 0%, #3a3a3a 55%, #2e2e2e 100%);
  }
  .back-brand {
    position: absolute;
    top: 50%;
    left: 50%;
    transform: translate(-50%, -50%);
    display: flex;
    align-items: center;
    gap: 8px;
  }
  .back-brand .brand-name { font-size: 24px; }
  .back-brand .brand-mark { width: 10px; height: 10px; }
</style>
</head>
<body>

  <section class="card card-front" aria-label="Business card front">
    <div class="brand">
      <span class="brand-mark"></span>
      <span class="brand-name">Varko Works</span>
    </div>
    <div class="rule rule-brand"></div>

    <div class="person">
      <p class="person-name">Daniel Reyes</p>
      <p class="person-title">Manager</p>
    </div>

    <div class="rule rule-main"></div>

    <ul class="contacts">
      <li>
        <svg viewBox="0 0 24 24" aria-hidden="true"><path d="M6.6 10.8a15 15 0 0 0 6.6 6.6l2.2-2.2a1 1 0 0 1 1-.25 11.4 11.4 0 0 0 3.6.57 1 1 0 0 1 1 1V20a1 1 0 0 1-1 1A17 17 0 0 1 3 4a1 1 0 0 1 1-1h3.5a1 1 0 0 1 1 1c0 1.25.2 2.45.57 3.6a1 1 0 0 1-.25 1z"/></svg>
        (253) 617-4930
      </li>
      <li>
        <svg viewBox="0 0 24 24" aria-hidden="true"><path d="M2 5h20v2l-10 7L2 7z M2 9l10 7 10-7v10H2z"/></svg>
        martin@plumlinegroup.com
      </li>
      <li>
        <svg viewBox="0 0 24 24" aria-hidden="true"><circle cx="12" cy="12" r="10"/></svg>
        www.varkoworks.com
      </li>
    </ul>

    <address class="address">
      18761 52nd Avenue S<br>
      Kent, WA 98047
    </address>
  </section>

  <section class="card card-back" aria-label="Business card back">
    <div class="pattern-field" role="img" aria-label="Repeating tone-on-tone embossed brand name pattern"></div>
    <div class="back-brand">
      <span class="brand-mark"></span>
      <span class="brand-name">Varko Works</span>
    </div>
  </section>

</body>
</html>
```